i need a business card for a plumbing company in california

we are a drain cleaning , maintenance plumbing company who is starting new marketing campaign for a tatrench-less pipe installation department .

Target Market(s)

the professional who appreciates time and quality workmanship.

Industry/Entity Type

Plumbing

Colors
0655a3
ec1f27

Requirements
Must have
• the second logo needs to be included
Nice to have
• a focus on the services offered
Should not have
• any underlined words on the brief

```html
<!DOCTYPE html>
<html lang="en">
<head>
<meta charset="utf-8">
<title>Clearline Plumbing – Business Card</title>
<link href="https://fonts.googleapis.com/css2?family=Arimo:wght@400;700&display=swap" rel="stylesheet">
<style>
  :root {
    --stage: #2b2b2b;
    --brand-red: #e0282b;
    --paper: #ffffff;
    --arc-grey: #85837a;
    --logo-grey: #7d7b73;
    --ink-light: #ffffff;
  }
  * { box-sizing: border-box; margin: 0; padding: 0; }
  html, body {
    width: 1200px; height: 880px; overflow: hidden;
    background: var(--stage);
    font-family: "Arimo", Arial, sans-serif;
  }
  .canvas { position: relative; width: 1200px; height: 880px; }

  .card {
    position: absolute;
    width: 640px; height: 366px;
    border-radius: 26px;
    overflow: hidden;
  }
  .card--front { left: 200px; top: 54px; background: var(--brand-red); }
  .card--back  { left: 360px; top: 460px; background: var(--brand-red); }

  .brand {
    position: absolute;
    display: flex; align-items: center; gap: 14px;
    font-weight: 700; line-height: 0.95;
  }
  .brand__mark { width: 22px; height: 22px; border-radius: 50%; flex: none; }
  .brand__name { font-size: 44px; letter-spacing: -0.5px; }

  .card--front .brand { left: 50%; top: 50%; transform: translate(-50%, -50%); }
  .card--front .brand__name { color: var(--ink-light); }
  .card--front .brand__mark { background: var(--ink-light); }

  .card--back .brand { left: 46px; top: 148px; }
  .card--back .brand__name { color: var(--logo-grey); font-size: 38px; }
  .card--back .brand__mark { background: var(--brand-red); }

  .back-shape { position: absolute; inset: 0; width: 640px; height: 366px; }

  .contact {
    position: absolute; left: 405px; top: 56px;
    color: var(--ink-light);
  }
  .contact__name { font-size: 22px; font-weight: 700; line-height: 1; }
  .contact__role { font-size: 14px; margin-top: 3px; }
  .contact__address { font-size: 14px; line-height: 1.3; margin-top: 30px; }
  .contact__list { list-style: none; margin-top: 16px; font-size: 14px; }
  .contact__list li { display: flex; align-items: center; gap: 9px; height: 24px; white-space: nowrap; }
  .contact__icon { width: 18px; height: 18px; flex: none; }
</style>
</head>
<body>
<main class="canvas">

  <section class="card card--front" aria-label="Card front">
    <div class="brand">
      <span class="brand__name">Clearline<br>Plumbing</span>
      <span class="brand__mark"></span>
    </div>
  </section>

  <section class="card card--back" aria-label="Card back">
    <svg class="back-shape" viewBox="0 0 640 366" aria-hidden="true">
      <path d="M250 0 C365 25 410 250 360 366 L340 366 C390 250 350 30 250 0 Z" fill="var(--arc-grey)"/>
      <path d="M250 0 C350 30 390 250 340 366 L0 366 L0 0 Z" fill="var(--paper)"/>
    </svg>

    <div class="brand">
      <span class="brand__name">Clearline<br>Plumbing</span>
      <span class="brand__mark"></span>
    </div>

    <div class="contact">
      <p class="contact__name">Dana Morales</p>
      <p class="contact__role">Manager</p>
      <p class="contact__address">PO BOX 418 Harbor Road<br>Oakdale, California</p>
      <ul class="contact__list">
        <li>
          <svg class="contact__icon" viewBox="0 0 18 18" aria-hidden="true">
            <circle cx="9" cy="9" r="8" fill="none" stroke="#fff" stroke-width="1.3"/>
            <rect x="6" y="4.5" width="6" height="9" rx="1" fill="none" stroke="#fff" stroke-width="1.2"/>
          </svg>
          555 014 2290
        </li>
        <li>
          <svg class="contact__icon" viewBox="0 0 18 18" aria-hidden="true">
            <circle cx="9" cy="9" r="8" fill="none" stroke="#fff" stroke-width="1.3"/>
            <rect x="4.5" y="6" width="9" height="6" fill="none" stroke="#fff" stroke-width="1.2"/>
            <path d="M4.5 6 L9 9.5 L13.5 6" fill="none" stroke="#fff" stroke-width="1.2"/>
          </svg>
          info@clearlineplumbing.com
        </li>
        <li>
          <svg class="contact__icon" viewBox="0 0 18 18" aria-hidden="true">
            <circle cx="9" cy="9" r="8" fill="none" stroke="#fff" stroke-width="1.3"/>
            <circle cx="9" cy="9" r="4.5" fill="none" stroke="#fff" stroke-width="1.1"/>
            <path d="M4.5 9 H13.5 M9 4.5 C7 7 7 11 9 13.5 M9 4.5 C11 7 11 11 9 13.5" fill="none" stroke="#fff" stroke-width="1"/>
          </svg>
          www.clearlineplumbing.com
        </li>
      </ul>
    </div>
  </section>

</main>
</body>
</html>
```